Fine Art business needs new website

We need a simple website with a home page, about us page, New sculptures, Sold sculptures, and a contact us page.Our sculptures are very high end one of a kind pieces. As such we need the site to be VERY elegant and professional. Lastly, because I'll be updating pictures on the website on a monthly basis it needs to be user friendly to update (Wordpress is preferred). The only branding we have so far for the business is a business card.
Updates
I wasn't completely ready when this project launched, also I am on the road right now and haven't been able to be as responsive to all you designers as I would like. I will work on giving feedback to all the top designs we've received so far. Thank you all so much for your participation and hardwork.
Target Market(s)
High end customers (affluent), art collectors, interior decorators/designers
Industry/Entity Type
Art Gallery
Coding
Coded - Design and coding required
Number of Pages Required
5+ page
Requirements
Must have
- Easily editable picture gallery for myself so that I can add new pieces(pictures of the pieces), remove sold pieces, etc. I would like the website to be built in wordpress so I can update it. I currently use mangewordpress through Netmarro for my other business website and would like to do the same for this one.
- Pages:
- -Intro page with featured pieces
- -Current pieces gallery (for sale) mainly a picture gallery
- -Sculptures archive (sold pieces) another picture gallery
- -About us: Pull-down of -about the artist (attached content)
- -Artistic Process (attached content)
- -Show Schedule:
- -one page dedicated to "friends of TMV" (basically a link page)
- TO BE CLEAR "www.pineroverslane.com" IS A TOTALLY DIFFERENT SITE AND I'M NOT TRYING TO COMBINE THE TWO OR JOIN THEM INTO ONE. This page needs be more elegant and seperate from the Pine Rovers site.
- UPDATE: I'd like a link to the TMV Facebook page: https://www.faceplume-social.com/mirelcraftworks/
Nice to have
- I would like the pictures on the gallery pages able to have text connected with them (Materials, price)
- I would like the site style and fonts to be similar to our business cards we've already had designed (picture attached).
Should not have
- Too much flash or other things that will make the site slow to load.

```html
<!DOCTYPE html>
<html lang="en">
<head>
<meta charset="utf-8">
<title>Stone Art Gallery</title>
<link href="https://fonts.googleapis.com/css2?family=Lato:wght@400;700&display=swap" rel="stylesheet">
<style>
:root{
  --page:#4a4a4a;
  --header-top:#3b3b3b;
  --header-bottom:#202020;
  --nav:#8a8a8a;
  --title:#8f8f8f;
  --intro:#707070;
  --card:#232323;
  --label:#2a2a2a;
  --price:#353535;
  --footer:#262626;
  --footer-head:#5e5e5e;
  --footer-text:#555555;
  --modal:#0b0b0b;
  --caption:rgba(0,0,0,.82);
  --caption-text:#e6e6e6;
  --arrow:#f2f2f2;
}
*{margin:0;padding:0;box-sizing:border-box}
html,body{width:1200px;height:2439px;overflow:hidden}
body{position:relative;background:var(--page);font-family:'Lato',sans-serif}

.site-header{position:absolute;left:0;top:0;width:1200px;height:296px;
  background:radial-gradient(ellipse at 80% 20%,#474747 0%,transparent 55%),linear-gradient(180deg,var(--header-top),var(--header-bottom))}
.main-nav{position:absolute;top:30px;left:0;width:1200px;height:16px;font-size:13px;font-weight:700;color:var(--nav);text-transform:uppercase}
.main-nav a{position:absolute;color:inherit;text-decoration:none}
.nav-active{border-bottom:1px solid var(--nav);padding-bottom:5px}
.nav-caret{display:inline-block;margin-left:6px;vertical-align:2px}
.menu-toggle{position:absolute;left:977px;top:28px}
.page-title{position:absolute;top:90px;width:1200px;text-align:center;font-size:27px;font-weight:700;color:var(--title);letter-spacing:.5px}
.title-rule{position:absolute;top:133px;left:568px;width:64px;height:1px;background:var(--nav)}
.page-intro{position:absolute;top:161px;left:220px;width:760px;text-align:center;font-size:16px;line-height:26px;color:var(--intro)}

.sort-select{position:absolute;left:857px;top:340px;width:154px;height:42px;border:1.5px solid #2b2b2b;color:#262626;font-size:12px;font-weight:700;display:flex;align-items:center;justify-content:center;gap:8px}

.sculpture{position:absolute;width:248px}
.sculpture-photo{width:248px;height:343px;border-radius:4px;background:var(--card);box-shadow:0 2px 5px rgba(0,0,0,.35)}
.sculpture-name{margin-top:23px;text-align:center;font-size:16px;color:var(--label)}
.sculpture-price{margin-top:4px;text-align:center;font-size:12px;color:var(--price)}

.pagination{position:absolute;top:2171px;left:530px;display:flex;align-items:flex-end;gap:10px}
.page-link{width:31px;height:31px;border:1.5px solid #2b2b2b;border-radius:3px;font-size:15px;color:#2b2b2b;display:flex;align-items:center;justify-content:center}
.page-gap{font-size:20px;font-weight:700;color:#2b2b2b;line-height:20px;margin:0 -6px}

.site-footer{position:absolute;left:0;top:2229px;width:1200px;height:210px;background:var(--footer)}
.footer-col{position:absolute;top:37px}
.footer-title{font-size:21px;font-weight:700;color:var(--footer-head);text-transform:uppercase}
.footer-about{margin-top:8px;font-size:12px;line-height:21px;color:var(--footer-text);width:220px}
.contact-line{display:flex;align-items:center;gap:10px;font-size:12px;line-height:21px;color:var(--footer-text)}
.footer-link{margin-top:3px;margin-left:24px;font-size:12px;font-weight:700;color:var(--footer-head)}
.social-row{margin-top:12px;display:flex;gap:8px;justify-content:center}
.social-square{width:19px;height:19px;border-radius:2px}

.lightbox{position:absolute;left:335px;top:725px;width:512px;height:691px;background:var(--modal);border:1px solid #333;box-shadow:0 0 12px rgba(0,0,0,.6)}
.lightbox-photo{position:absolute;inset:0;background:radial-gradient(ellipse 18% 48% at 50% 46%,#5f9a77 0%,#3e7a58 40%,#23382c 70%,transparent 100%),linear-gradient(180deg,#161616,#0a0a0a)}
.lightbox-caption{position:absolute;left:0;bottom:0;width:100%;height:231px;background:var(--caption);color:var(--caption-text);padding:26px 37px 0}
.caption-label{font-size:17px}
.caption-text{margin-top:27px;margin-left:3px;font-size:16.5px;line-height:26px;width:385px}
.lightbox-arrow{position:absolute;top:1043px}
</style>
</head>
<body>

<header class="site-header">
  <nav class="main-nav">
    <a style="left:193px">Home</a>
    <a style="left:257px">About<svg class="nav-caret" width="9" height="6" viewBox="0 0 9 6"><path d="M1 1l3.5 3.5L8 1" fill="none" stroke="#8a8a8a" stroke-width="1.3"/></svg></a>
    <a class="nav-active" style="left:343px">Gallery</a>
    <a style="left:424px">Contact</a>
  </nav>
  <svg class="menu-toggle" width="35" height="20" viewBox="0 0 35 20" aria-label="Menu"><g stroke="#8a8a8a" stroke-width="2.4"><path d="M0 2h35M0 10h35M0 18h35"/></g></svg>
  <h1 class="page-title">STONE ART GALLERY</h1>
  <div class="title-rule"></div>
  <p class="page-intro">Lorem ipsum dolor sit amet, consectetur adipiscing elit. Donec vulputate ac velit et sagittis. Phasellus fermentum lacinia eros, at blandit tellus vestibulum sit amet. Fusce ultricies felis lorem, et ullamcorper urna feugiat ac.</p>
</header>

<div class="sort-select">Default Sorting <svg width="10" height="6" viewBox="0 0 10 6"><path d="M1 1l4 4 4-4" fill="none" stroke="#262626" stroke-width="1.3"/></svg></div>

<main class="gallery">
  <article class="sculpture" style="left:189px;top:434px"><div class="sculpture-photo" role="img" aria-label="Green malachite sculpture on a round pedestal" style="background:radial-gradient(ellipse 26% 40% at 50% 42%,#2f5a45,#1d3a2c 60%,var(--card) 100%)"></div><p class="sculpture-name">Sculpture Name</p><p class="sculpture-price">$179</p></article>
  <article class="sculpture" style="left:476px;top:434px"><div class="sculpture-photo" role="img" aria-label="Brown agate slice sculpture on a stand" style="background:radial-gradient(ellipse 22% 40% at 50% 40%,#5a4030,#3a2a20 60%,var(--card) 100%)"></div><p class="sculpture-name">Sculpture Name</p><p class="sculpture-price">$179</p></article>
  <article class="sculpture" style="left:763px;top:434px"><div class="sculpture-photo" role="img" aria-label="Blue crystal geode column sculpture" style="background:radial-gradient(ellipse 24% 42% at 50% 45%,#3e4a6e,#2a3048 60%,var(--card) 100%)"></div><p class="sculpture-name">Sculpture Name</p><p class="sculpture-price">$179</p></article>

  <article class="sculpture" style="left:189px;top:863px"><div class="sculpture-photo" role="img" aria-label="Purple amethyst geode sculpture on a stand" style="background:radial-gradient(ellipse 28% 38% at 50% 42%,#4a3a68,#302642 60%,var(--card) 100%)"></div><p class="sculpture-name">Sculpture Name</p><p class="sculpture-price">$179</p></article>
  <article class="sculpture" style="left:476px;top:863px"><div class="sculpture-photo" role="img" aria-label="Stone sculpture" style="background:radial-gradient(ellipse 24% 40% at 50% 45%,#3a3a3a,var(--card) 100%)"></div><p class="sculpture-name">Sculpture Name</p><p class="sculpture-price">$179</p></article>
  <article class="sculpture" style="left:763px;top:863px"><div class="sculpture-photo" role="img" aria-label="Green jade column sculpture" style="background:radial-gradient(ellipse 18% 42% at 50% 42%,#3e6a52,#26402f 60%,var(--card) 100%)"></div><p class="sculpture-name">Sculpture Name</p><p class="sculpture-price">$179</p></article>

  <article class="sculpture" style="left:189px;top:1293px"><div class="sculpture-photo" role="img" aria-label="Amber swirled stone sculpture" style="background:radial-gradient(ellipse 26% 40% at 50% 45%,#6a4a24,#3e2c18 60%,var(--card) 100%)"></div><p class="sculpture-name">Sculpture Name</p><p class="sculpture-price">$179</p></article>
  <article class="sculpture" style="left:476px;top:1293px"><div class="sculpture-photo" role="img" aria-label="Stacked geode sculpture on a pedestal" style="background:radial-gradient(ellipse 24% 42% at 50% 48%,#4a3a40,#2e2628 60%,var(--card) 100%)"></div><p class="sculpture-name">Sculpture Name</p><p class="sculpture-price">$179</p></article>
  <article class="sculpture" style="left:763px;top:1293px"><div class="sculpture-photo" role="img" aria-label="Pale coral fossil stone sculpture" style="background:radial-gradient(ellipse 24% 42% at 50% 42%,#8a7a62,#4a4034 60%,var(--card) 100%)"></div><p class="sculpture-name">Sculpture Name</p><p class="sculpture-price">$179</p></article>

  <article class="sculpture" style="left:189px;top:1722px"><div class="sculpture-photo" role="img" aria-label="Amethyst geode sculpture on a dark base" style="background:radial-gradient(ellipse 26% 40% at 50% 40%,#4a3454,#2e2434 60%,var(--card) 100%)"></div><p class="sculpture-name">Sculpture Name</p><p class="sculpture-price">$179</p></article>
  <article class="sculpture" style="left:476px;top:1722px"><div class="sculpture-photo" role="img" aria-label="Orange crystal geode sculpture on a base" style="background:radial-gradient(ellipse 28% 34% at 50% 42%,#7a5030,#45301e 60%,var(--card) 100%)"></div><p class="sculpture-name">Sculpture Name</p><p class="sculpture-price">$179</p></article>
  <article class="sculpture" style="left:763px;top:1722px"><div class="sculpture-photo" role="img" aria-label="Blue lace agate slab sculpture" style="background:radial-gradient(ellipse 22% 44% at 50% 42%,#5a6a80,#343c48 60%,var(--card) 100%)"></div><p class="sculpture-name">Sculpture Name</p><p class="sculpture-price">$179</p></article>
</main>

<div class="pagination">
  <span class="page-link">1</span>
  <span class="page-link">2</span>
  <span class="page-gap">...</span>
  <span class="page-link">10</span>
</div>

<footer class="site-footer">
  <div class="footer-col" style="left:197px">
    <h2 class="footer-title">About Us</h2>
    <p class="footer-about">This is a dummy text just<br>to provide text in the About Us<br>section which will be added correctly<br>later on.</p>
  </div>
  <div class="footer-col" style="left:527px">
    <h2 class="footer-title">Our Address</h2>
    <div style="margin-top:8px">
      <p class="contact-line"><svg width="13" height="13" viewBox="0 0 13 13"><path d="M3 1l2 3-1.3 1.3a7 7 0 003.9 3.9L9 8l3 2-1.3 2C6 12 1 7 1 2.3z" fill="#5e5e5e"/></svg>(555) 014-2290</p>
      <p class="contact-line"><svg width="14" height="10" viewBox="0 0 14 10"><rect x=".5" y=".5" width="13" height="9" fill="none" stroke="#5e5e5e"/><path d="M.5 .5l6.5 5 6.5-5" fill="none" stroke="#5e5e5e"/></svg>mara@pineroverslane.com</p>
      <p class="contact-line"><svg width="13" height="13" viewBox="0 0 13 13"><g fill="none" stroke="#5e5e5e" stroke-width="1.4"><path d="M5.5 7.5l2-2"/><path d="M6 3.5l1.5-1.5a2.5 2.5 0 013.5 3.5L9.5 7"/><path d="M7 9.5L5.5 11A2.5 2.5 0 012 7.5L3.5 6"/></g></svg>www.tmvstudio-art.com</p>
      <p class="footer-link">CONTACT US</p>
    </div>
  </div>
  <div class="footer-col" style="left:854px;width:157px;text-align:center">
    <h2 class="footer-title">Keep in Touch</h2>
    <div class="social-row">
      <span class="social-square" style="background:#3a6a8a" role="img" aria-label="Social link"></span>
      <span class="social-square" style="background:#7a2a30" role="img" aria-label="Social link"></span>
      <span class="social-square" style="background:#34487a" role="img" aria-label="Social link"></span>
      <span class="social-square" style="background:#4a5a68" role="img" aria-label="Social link"></span>
    </div>
  </div>
</footer>

<div class="lightbox">
  <div class="lightbox-photo" role="img" aria-label="Tall green jade sculpture shown large"></div>
  <div class="lightbox-caption">
    <p class="caption-label">Materials Used:</p>
    <p class="caption-text">Lorem ipsum dolor sit amet, consectetur adipiscing elit. Donec vulputate ac velit et sagittis. Phasellus fermentum lacinia eros, at blandit tellus vestibulum sit amet. Fusce ultricies felis lorem, et ullamcorper urna feugiat ac.</p>
  </div>
</div>
<svg class="lightbox-arrow" style="left:234px" width="56" height="56" viewBox="0 0 56 56" aria-label="Previous"><g fill="none" stroke="#f2f2f2" stroke-width="5"><path d="M27 4L4 28l23 24"/><path d="M50 4L27 28l23 24"/></g></svg>
<svg class="lightbox-arrow" style="left:892px" width="56" height="56" viewBox="0 0 56 56" aria-label="Next"><g fill="none" stroke="#f2f2f2" stroke-width="5"><path d="M6 4l23 24L6 52"/><path d="M29 4l23 24-23 24"/></g></svg>

</body>
</html>
```